HOME PAGE AND AND SECONDARY DESIGN FOR INTERNAL PAGES

Construction company looking for an easy to navagate professional serious greyscale website with a good clean feel simple clean menu and responsive friendly design. Our main clientele is commercial properties business owners and investors of rental properties. This website is going to be static HTML5 and would need multiple sizing files for clean fast rendering. Clean and accurate design files a must so if your experienced awesome modern greyscale designer let's get started I need this done as soon as possible.

Industry/Entity Type

construction, electrical, plumbing, commercial build outs

Number of Pages Required

2 page

Font styles to use
Sans Serif

Colors

Designer to choose only greyscale colors for use in the design.

Requirements
Must have
• Main Menu... Home, Services, Projects, About our team

```html
<!DOCTYPE html>
<html lang="en">
<head>
<meta charset="utf-8">
<title>Granite Works — Home</title>
<link href="https://fonts.googleapis.com/css2?family=Roboto:wght@300;400;500;700&display=swap" rel="stylesheet">
<style>
:root{
  --ink:#1f1f1f;
  --text:#333;
  --muted:#777;
  --light:#bdbdbd;
  --faint:#ececec;
  --panel:#f4f4f4;
  --white:#fff;
  --dark:#2b2b2b;
  --footer:#2d2d2d;
  --line:#d6d6d6;
}
*{margin:0;padding:0;box-sizing:border-box}
html,body{width:1200px;height:3372px;overflow:hidden;background:var(--white)}
body{font-family:"Roboto",Arial,sans-serif;color:var(--text);position:relative}
.abs{position:absolute}
.brand{display:flex;align-items:center;gap:8px;font-size:13px;font-weight:700;letter-spacing:1px;color:var(--ink)}
.brand .dot{width:14px;height:14px;background:var(--ink);border-radius:50%}
.nav{left:596px;top:30px;display:flex;gap:30px;font-size:10px;letter-spacing:1.5px;color:var(--text)}
.nav a{color:inherit;text-decoration:none;padding:4px 10px}
.nav a.active{border:1px solid var(--ink)}

/* photo placeholders: soft tonal gradients */
.ph-hero{background:
  radial-gradient(ellipse 60% 45% at 62% 38%,#ffffff 0%,rgba(255,255,255,0) 70%),
  radial-gradient(ellipse 40% 50% at 85% 70%,#9c9c9c 0%,rgba(156,156,156,0) 70%),
  linear-gradient(175deg,#e9e9e9 0%,#d9d9d9 40%,#c4c4c4 75%,#a8a8a8 100%)}
.ph-glass{background:
  radial-gradient(ellipse 70% 60% at 30% 30%,#d8d8d8 0%,rgba(216,216,216,0) 70%),
  linear-gradient(135deg,#bdbdbd 0%,#8f8f8f 55%,#6e6e6e 100%)}
.ph-tower{background:
  radial-gradient(ellipse 50% 70% at 65% 55%,#a6a6a6 0%,rgba(166,166,166,0) 70%),
  linear-gradient(180deg,#f2f2f2 0%,#d2d2d2 50%,#b8b8b8 100%)}
.ph-angle{background:
  radial-gradient(ellipse 45% 60% at 40% 50%,#111 0%,rgba(17,17,17,0) 75%),
  linear-gradient(120deg,#f0f0f0 0%,#c8c8c8 40%,#3a3a3a 60%,#e6e6e6 100%)}
.ph-sample{background:
  linear-gradient(90deg,rgba(40,40,40,.85) 0%,rgba(40,40,40,.55) 55%,rgba(40,40,40,.25) 100%),
  radial-gradient(ellipse 50% 60% at 75% 45%,#a0a0a0 0%,rgba(160,160,160,0) 70%),
  linear-gradient(160deg,#5a5a5a 0%,#3a3a3a 100%)}
.ph-roof{background:
  radial-gradient(ellipse 55% 80% at 55% 90%,#ffffff 0%,#f0f0f0 35%,rgba(240,240,240,0) 72%),
  linear-gradient(180deg,#3c3c3c 0%,#6a6a6a 45%,#bdbdbd 80%,#e9e9e9 100%)}
.ph-aerial{background:
  radial-gradient(ellipse 45% 40% at 45% 45%,#e2e2e2 0%,rgba(226,226,226,0) 70%),
  linear-gradient(150deg,#7a7a7a 0%,#4a4a4a 60%,#2e2e2e 100%)}
.ph-apart{background:
  radial-gradient(ellipse 70% 45% at 50% 65%,#f2f2f2 0%,rgba(242,242,242,0) 70%),
  linear-gradient(180deg,#b9b9b9 0%,#d6d6d6 35%,#8c8c8c 75%,#5c5c5c 100%)}
.ph-arch{background:
  radial-gradient(ellipse 60% 55% at 45% 60%,#ffffff 0%,rgba(255,255,255,0) 70%),
  linear-gradient(180deg,#7d7d7d 0%,#bcbcbc 40%,#e6e6e6 70%,#9a9a9a 100%)}
.ph-call{background:
  radial-gradient(ellipse 14% 30% at 52% 25%,#2e2e2e 0%,rgba(46,46,46,0) 75%),
  radial-gradient(ellipse 28% 55% at 66% 80%,#e0e0e0 0%,rgba(224,224,224,0) 75%),
  linear-gradient(90deg,#fbfbfb 0%,#f3f3f3 30%,#c9c9c9 60%,#ededed 100%)}

.hero-photo{left:448px;top:88px;width:640px;height:672px}
.hero-title{left:112px;top:358px}
.hero-title .kicker{font-size:52px;font-weight:300;color:var(--light);letter-spacing:1px;line-height:1}
.hero-title .name{font-size:52px;font-weight:500;color:var(--ink);line-height:1.1}
.pager{left:112px;top:548px;display:flex}
.pager span{width:44px;height:36px;display:flex;align-items:center;justify-content:center;border:1px solid var(--line)}
.pager span+span{border-left:none}
.hero-social{left:112px;top:668px;display:flex;gap:24px}
.hero-social i{width:14px;height:14px;border:1.5px solid var(--muted);border-radius:50%;display:block}
.view-btn{left:448px;top:722px;background:var(--white);padding:14px 24px;font-size:10px;letter-spacing:1.5px;color:var(--ink);display:flex;gap:14px;align-items:center}

.about-panel{left:112px;top:872px;width:976px;height:328px;background:var(--panel)}
.about h2{font-size:58px;font-weight:300;color:var(--light);line-height:1}
.about p{font-size:12.5px;line-height:1.65;color:var(--text);width:380px;margin-top:16px}
.more{font-size:10px;letter-spacing:1.5px;color:var(--ink);display:flex;gap:12px;align-items:center;margin-top:34px}

.section-title{left:112px;font-size:54px;font-weight:300;color:var(--light);line-height:1}
.focus .num{position:absolute;left:0;top:0;font-size:180px;font-weight:300;color:var(--faint);line-height:.8}
.focus p{position:absolute;left:112px;top:4px;font-size:19px;line-height:1.75;color:var(--ink);width:330px}

.sample{left:112px;top:1788px;width:476px;height:212px}
.sample h3{position:absolute;left:64px;top:46px;font-size:46px;font-weight:700;color:var(--white);line-height:1.1}
.sample span{position:absolute;left:64px;top:158px;font-size:9px;letter-spacing:1.5px;color:#ddd}
.btn-dark{background:var(--dark);color:var(--white);font-size:10px;letter-spacing:1.5px;display:flex;align-items:center;justify-content:center;gap:14px}
.field{left:112px;width:328px;height:36px;background:var(--panel);font-size:10px;color:#999;padding:12px 10px}

.footer{left:0;top:3028px;width:1200px;height:344px;background:var(--footer);color:#cfcfcf}
.footer .brand{color:var(--white)}
.footer .brand .dot{background:var(--white)}
.footer h4{font-size:12px;font-weight:500;color:var(--white);margin-bottom:12px}
.footer li{list-style:none;font-size:11px;line-height:2.1;color:#cfcfcf}
.footer .blurb{font-size:11px;line-height:1.7;width:420px}
.social{display:flex;gap:22px;margin-bottom:26px}
.social i{width:14px;height:14px;background:#cfcfcf;display:block;border-radius:50%}
.contact-line{display:flex;gap:12px;font-size:11px;line-height:1.5;margin-bottom:10px}
.copy{position:absolute;left:0;right:0;top:3340px;text-align:center;font-size:9px;color:#888}
</style>
</head>
<body>

<header>
  <div class="abs brand" style="left:112px;top:34px"><span class="dot"></span>GRANITE WORKS</div>
  <nav class="abs nav">
    <a class="active">HOME</a><a>SERVICES</a><a>PROJECTS</a><a>ABOUT US</a><a>OUR TEAM</a>
  </nav>
</header>

<section class="hero">
  <div class="abs hero-photo ph-hero" role="img" aria-label="Modern white multi-storey building with stacked balconies seen from below"></div>
  <div class="abs hero-title">
    <div class="kicker">PROJECT</div>
    <div class="name">Lorum</div>
  </div>
  <div class="abs pager">
    <span><svg width="14" height="8"><path d="M14 4H2M5 1L2 4l3 3" stroke="#333" fill="none"/></svg></span>
    <span><svg width="14" height="8"><path d="M0 4h12M9 1l3 3-3 3" stroke="#333" fill="none"/></svg></span>
  </div>
  <div class="abs hero-social"><i></i><i></i><i></i></div>
  <div class="abs view-btn">VIEW PROJECT <svg width="14" height="8"><path d="M0 4h12M9 1l3 3-3 3" stroke="#333" fill="none"/></svg></div>
</section>

<section class="about">
  <div class="abs about-panel"></div>
  <div class="abs ph-glass" style="left:192px;top:900px;width:228px;height:220px" role="img" aria-label="Glass tower facade"></div>
  <div class="abs ph-tower" style="left:440px;top:928px;width:232px;height:280px" role="img" aria-label="High-rise office building against the sky"></div>
  <div class="abs ph-angle" style="left:192px;top:1140px;width:228px;height:124px" role="img" aria-label="Angular building corner detail"></div>
  <div class="abs" style="left:696px;top:892px">
    <h2>About</h2>
    <p>Lorem Ipsum is simply dummy text of the printing and typesetting industry. Lorem Ipsum has been the industry's standard dummy text ever since the 1500s, when an unknown printer took a galley of type and scrambled it to make a type specimen book. It has survived not only five centuries, but also the leap into electronic typesetting, remaining essentially unchanged.</p>
    <div class="more">READ MORE <svg width="14" height="8"><path d="M0 4h12M9 1l3 3-3 3" stroke="#333" fill="none"/></svg></div>
  </div>
</section>

<section>
  <h2 class="abs section-title" style="top:1362px">Main Focus/Mission Statement</h2>
  <div class="abs focus" style="left:112px;top:1464px"><div class="num">1</div><p>Lorem ipsum dolor sit amet, consectetur adipiscing elit. Sed efficitur, lectus et facilisis placerat.</p></div>
  <div class="abs focus" style="left:612px;top:1464px"><div class="num">2</div><p>Lorem ipsum dolor sit amet, consectetur adipiscing elit. Sed efficitur, lectus et facilisis placerat, magna mauris porttitor tortor, a auctor est felis ut nisl.</p></div>
</section>

<section>
  <h2 class="abs section-title" style="top:1688px">Our Projects</h2>
  <div class="abs sample ph-sample" role="img" aria-label="Featured project: modern commercial building exterior">
    <h3>Sample<br>Project</h3><span>VIEW MORE &rarr;</span>
  </div>
  <div class="abs ph-roof" style="left:612px;top:1788px;width:476px;height:212px" role="img" aria-label="Curved white ribbed roof structure under a dark sky"></div>
  <div class="abs ph-aerial" style="left:112px;top:2028px;width:224px;height:212px" role="img" aria-label="Aerial view of a commercial building"></div>
  <div class="abs ph-apart" style="left:364px;top:2028px;width:388px;height:212px" role="img" aria-label="Apartment complex with trees in front"></div>
  <div class="abs ph-arch" style="left:780px;top:2028px;width:308px;height:212px" role="img" aria-label="Modern arched white building"></div>
  <div class="abs btn-dark" style="left:908px;top:2262px;width:180px;height:58px">ALL PROJECTS <svg width="14" height="8"><path d="M0 4h12M9 1l3 3-3 3" stroke="#fff" fill="none"/></svg></div>
</section>

<section>
  <h2 class="abs section-title" style="top:2418px">Contact Us</h2>
  <div class="abs field" style="top:2496px">Name</div>
  <div class="abs field" style="top:2544px">Phone Number*</div>
  <div class="abs field" style="top:2592px">E-mail*</div>
  <div class="abs field" style="top:2640px">Company ID</div>
  <div class="abs field" style="top:2688px;height:112px">Message*</div>
  <div class="abs ph-call" style="left:464px;top:2496px;width:624px;height:304px" role="img" aria-label="Businessman in a white shirt talking on the phone"></div>
  <div class="abs btn-dark" style="left:112px;top:2864px;width:184px;height:58px">SEND EMAIL <svg width="14" height="8"><path d="M0 4h12M9 1l3 3-3 3" stroke="#fff" fill="none"/></svg></div>
</section>

<footer class="abs footer">
  <div class="abs brand" style="left:168px;top:44px"><span class="dot"></span>GRANITE WORKS</div>
  <p class="abs blurb" style="left:168px;top:152px">Lorem ipsum is simply dummy text of the printing and typesetting industry. Lorem ipsum has been the industry's standard dummy text ever since the 1500s, when an unknown printer took a galley of type and scrambled it to make a type specimen book. It has survived not only five centuries but also the leap into electronic typesetting, remaining essentially unchanged.</p>
  <div class="abs" style="left:648px;top:44px">
    <h4>Information</h4>
    <ul><li>Main</li><li>Services</li><li>Projects</li><li>About Us</li><li>Our Team</li></ul>
  </div>
  <div class="abs" style="left:864px;top:44px">
    <h4>Social Media</h4>
    <div class="social"><i></i><i></i><i></i><i></i></div>
    <h4>Contacts</h4>
    <div class="contact-line"><svg width="10" height="14"><path d="M5 13C1 8 1 6 1 5a4 4 0 018 0c0 1 0 3-4 8z" fill="#cfcfcf"/></svg><span>88 Quarry Lane<br>Stoneford TX 70000</span></div>
    <div class="contact-line"><svg width="10" height="12"><rect x="1" y="0" width="8" height="12" rx="2" fill="#cfcfcf"/></svg><span>555-014-2290</span></div>
    <div class="contact-line"><svg width="12" height="10"><rect x="0" y="1" width="12" height="8" fill="none" stroke="#cfcfcf"/><path d="M0 1l6 5 6-5" fill="none" stroke="#cfcfcf"/></svg><span>hello@graniteworks.test</span></div>
  </div>
</footer>
<div class="copy">© 2024 Granite Works</div>

</body>
</html>
```